Ductless Mini Split Business Website

Copper Fern Services is looking to design an eye catching educational website about installing Ductless mini splits.

Similar to this company.
https://www.halvikstream.com/

Coding

Coded - Design and coding required

```html
<!DOCTYPE html>
<html lang="en">
<head>
<meta charset="utf-8">
<title>Copper Fern Services – Ductless Experts</title>
<link href="https://fonts.googleapis.com/css2?family=Lato:wght@400;700;900&display=swap" rel="stylesheet">
<style>
:root{
  --yellow:#fdd20a;
  --yellow-deep:#f5c400;
  --ink:#1e1e1e;
  --dark:#2e2e2e;
  --grey:#555;
  --muted:#777;
  --light:#e9e9e9;
  --white:#fff;
}
*{box-sizing:border-box;margin:0;padding:0}
html,body{width:1200px;height:3901px;overflow:hidden}
body{position:relative;font-family:'Lato',sans-serif;color:var(--ink);background:var(--white)}
.abs{position:absolute}
.btn{position:absolute;display:flex;align-items:center;justify-content:center;background:var(--yellow);border-radius:40px;font-weight:700;font-size:16px;color:var(--ink);box-shadow:0 0 0 3px var(--white),0 0 0 5px var(--yellow)}
.ph{position:absolute}

/* header */
.site-header{position:absolute;left:0;top:0;width:1200px;height:117px;background:var(--white)}
.brand{position:absolute;left:106px;top:22px;width:220px;text-align:center}
.brand-name{font-size:24px;font-weight:900;color:var(--ink);line-height:1.1}
.brand-tag{font-size:21px;font-weight:900;color:var(--ink);margin-top:12px;letter-spacing:.5px}
.call{position:absolute;right:76px;top:20px;font-size:19px;font-weight:900;display:flex;align-items:center;gap:8px}
.call span{color:var(--yellow)}
.nav a{position:absolute;top:76px;font-size:15px;color:var(--grey);text-decoration:none;letter-spacing:.2px}
.nav a.active{color:var(--ink);padding-bottom:18px;border-bottom:4px solid var(--yellow)}

/* hero */
.hero-card{position:absolute;left:139px;top:277px;width:479px;height:265px;background:rgba(40,40,40,.82);padding:42px 38px}
.hero-card h1{font-size:44px;font-weight:900;color:var(--white);line-height:1;text-transform:uppercase}
.hero-card p{font-size:17px;color:var(--white);margin-top:12px;font-weight:700}

/* about */
.about-box{position:absolute;left:520px;top:788px;width:591px;height:424px;background:var(--dark)}
.about-box .frame{position:absolute;inset:10px;border:1px solid #8a7a2a}
.about-box h2{position:absolute;left:120px;top:66px;font-size:33px;font-weight:700;color:var(--white)}
.about-box p{position:absolute;left:120px;width:420px;font-size:13px;line-height:22px;color:#ddd}

/* help */
.section-title{position:absolute;left:0;width:1200px;text-align:center;font-size:30px;font-weight:700;color:var(--ink)}
.service{position:absolute;top:1462px;width:245px;height:208px;border:3px solid var(--white);box-shadow:0 1px 4px rgba(0,0,0,.2)}
.service .label{position:absolute;left:6px;right:6px;bottom:4px;height:42px;background:#2b2b2b;color:var(--white);font-size:15px;font-weight:700;display:flex;align-items:center;justify-content:center}

/* why */
.why{position:absolute;top:2007px;width:299px;height:312px;border:2px solid #ddd;background:var(--white);padding:42px 38px}
.why.alt{background:var(--yellow);border-color:var(--yellow)}
.why h3{font-size:20px;font-weight:700;margin-top:18px;line-height:1.25}
.why p{font-size:14px;line-height:23px;color:var(--grey);margin-top:14px}
.why.alt p{color:#7a5b00}
.why.alt h3{color:#2a2a2a}

/* contact */
.field{position:absolute;background:var(--white);font-size:14px;color:var(--grey);padding:16px 18px}

/* blogs */
.post{position:absolute;top:3121px;width:299px;height:339px;background:var(--white);box-shadow:0 1px 5px rgba(0,0,0,.2)}
.post .img{position:absolute;left:0;top:0;width:100%;height:204px}
.post h4{position:absolute;left:30px;top:224px;font-size:17px;font-weight:700}
.post p{position:absolute;left:30px;top:251px;width:250px;font-size:12px;line-height:18px;color:var(--muted)}
.post .more{position:absolute;left:30px;top:302px;font-size:11px;font-weight:700}

/* footer */
.site-footer{position:absolute;left:0;top:3530px;width:1200px;height:308px;background:linear-gradient(180deg,#fdd20a,#f8c900)}
.foot-col h5{font-size:18px;font-weight:700;color:var(--ink);margin-bottom:14px}
.foot-col a,.foot-col div{display:block;font-size:15px;color:#4a3a00;text-decoration:none;line-height:25px}
.social{position:absolute;top:3709px;width:38px;height:38px;border-radius:50%;background:var(--ink)}
.copyright{position:absolute;left:0;top:3838px;width:1200px;height:63px;background:var(--ink);color:#ccc;font-size:13px;display:flex;align-items:center;justify-content:center}
</style>
</head>
<body>

<header class="site-header">
  <div class="brand">
    <div class="brand-name">Copper Fern Services</div>
    <div class="brand-tag">DUCTLESS EXPERTS</div>
  </div>
  <div class="call">
    <svg width="20" height="20" viewBox="0 0 24 24"><path fill="#fdd20a" d="M6.6 10.8a15.1 15.1 0 0 0 6.6 6.6l2.2-2.2c.3-.3.7-.4 1-.2 1.1.4 2.3.6 3.6.6.6 0 1 .4 1 1V20c0 .6-.4 1-1 1C10.6 21 3 13.4 3 4c0-.6.4-1 1-1h3.5c.6 0 1 .4 1 1 0 1.3.2 2.5.6 3.6.1.3 0 .7-.2 1z"/></svg>
    <span>Call Us Today</span> (503) 555 0148
  </div>
  <nav class="nav">
    <a class="active" style="left:406px">ABOUT US</a>
    <a style="left:514px">DUCTLESS HEAT PUMPS</a>
    <a style="left:718px">SERVICES</a>
    <a style="left:820px">TESTIMONIALS</a>
    <a style="left:957px">BLOG</a>
    <a style="left:1030px">CONTACT US</a>
  </nav>
</header>

<section class="hero">
  <div class="ph" role="img" aria-label="Living room with white sectional sofa, forest mural and wall-mounted mini split unit on a stone wall" style="left:0;top:117px;width:1200px;height:641px;background:linear-gradient(100deg,#3f5a3a 0%,#6c7f7a 30%,#a9a9b0 55%,#8f939a 75%,#c8cbd0 100%)"></div>
  <svg class="abs" style="left:0;top:640px" width="1200" height="125" viewBox="0 0 1200 125">
    <polygon points="650,72 1200,18 1200,102 0,118 0,125 1200,125" fill="#fdd20a"/>
    <polygon points="0,118 1200,102 1200,125 0,125" fill="#fff"/>
  </svg>
  <div class="hero-card">
    <h1>Ductless Mini<br>Splits Experts</h1>
    <p>LET HALVIK STREAM HEROES SHOW YOU HOW</p>
  </div>
  <div class="btn" style="left:180px;top:455px;width:184px;height:50px">CONTACT US</div>
</section>

<section class="about">
  <div class="ph" role="img" aria-label="Technician servicing an indoor mini split unit, video thumbnail" style="left:121px;top:848px;width:474px;height:309px;background:linear-gradient(135deg,#cfd6dc,#e8ecef 60%,#8da0b5)"></div>
  <svg class="abs" style="left:336px;top:968px" width="64" height="64" viewBox="0 0 64 64"><circle cx="32" cy="32" r="32" fill="#fff"/><polygon points="26,20 26,44 45,32" fill="#111"/></svg>
  <div class="about-box">
    <div class="frame"></div>
    <h2>COPPER FERN SERVICES</h2>
    <p style="top:128px">Fusce tellus Sed metus augue convallis et vehicula ut pulvinar eu ante Integer orci tellus tristique vitae consequat nec porta vel lectus Nulla sit amet diamaliquam enim Proin dui lectus</p>
    <p style="top:218px">cursus eu mattis laoreet viverra sit amet quam Curabitur vel dolor ultrices ipsum dictum tristique Praesent vitae lacus Ut velit enim vestibulum non fermentum nec hendrerit quis leo</p>
  </div>
  <div class="btn" style="left:640px;top:1102px;width:180px;height:48px">CONTACT US</div>
</section>

<section class="help">
  <div class="ph" role="img" aria-label="Faded grey snowy mountain range backdrop" style="left:0;top:1257px;width:1200px;height:652px;background:linear-gradient(180deg,#d6d6d6,#ececec 40%,#cfcfcf)"></div>
  <svg class="abs" style="left:0;top:1250px" width="1200" height="70" viewBox="0 0 1200 70">
    <polygon points="0,0 0,70 420,48" fill="#fdd20a"/>
    <polygon points="0,0 1200,0 1200,5 420,48 0,0" fill="#fff"/>
  </svg>
  <svg class="abs" style="left:0;top:1810px" width="1200" height="100" viewBox="0 0 1200 100">
    <polygon points="500,48 1200,8 1200,96" fill="#fdd20a"/>
    <polygon points="0,82 500,48 1200,96 1200,100 0,100" fill="#fff"/>
  </svg>
  <div class="section-title" style="top:1376px">HOW CAN WE HELP YOU?</div>
  <div class="service" style="left:83px"><div class="ph" role="img" aria-label="Technician fitting an indoor unit on a brick wall" style="inset:0;background:linear-gradient(135deg,#8b7d78,#d8d4cf)"></div><div class="label">DUCTESS EXPERT</div></div>
  <div class="service" style="left:347px"><div class="ph" role="img" aria-label="Technician installing a mini split" style="inset:0;background:linear-gradient(135deg,#d9c7b0,#cfd6de)"></div><div class="label">INSTALLATION</div></div>
  <div class="service" style="left:609px"><div class="ph" role="img" aria-label="Technician repairing an outdoor unit" style="inset:0;background:linear-gradient(135deg,#7f8a92,#3c4450)"></div><div class="label">DUCTLESS REPAIR</div></div>
  <div class="service" style="left:873px"><div class="ph" role="img" aria-label="Technician maintaining a condenser fan unit" style="inset:0;background:linear-gradient(135deg,#bfc3c7,#e9e6e2)"></div><div class="label">MAINTENANCE</div></div>
  <div class="btn" style="left:495px;top:1720px;width:199px;height:53px">VIEW MORE</div>
</section>

<section class="why-us">
  <div class="section-title" style="top:1936px">WHY CHOOSE US</div>
  <div class="why" style="left:136px">
    <svg width="72" height="70" viewBox="0 0 72 70" fill="none" stroke="#222" stroke-width="2"><circle cx="38" cy="20" r="14"/><text x="33" y="26" font-size="16" fill="#222" stroke="none" font-family="Lato,sans-serif">$</text><path d="M4 50l12-8h14l10 6H28M16 62l6-4h20l24-16c-3-4-8-3-10-1L42 50"/></svg>
    <h3>Money Back Gurantee</h3>
    <p>Praesent vitae lacus Ut velit enim vestibulum non fermentum nec hendrerit quis leo</p>
  </div>
  <div class="why alt" style="left:457px">
    <svg width="66" height="66" viewBox="0 0 66 66" fill="none" stroke="#222" stroke-width="2.5"><path d="M8 8l26 26M6 14l8-8 6 6-8 8zM34 34l4 4-4 4-4-4zM38 42l18 18 6-6-18-18"/><path d="M44 22a10 10 0 0 1 14-14l-7 7 1 5 5 1 7-7a10 10 0 0 1-14 14L22 56a4 4 0 0 1-6-6z"/></svg>
    <h3>Expert Services</h3>
    <p>Praesent vitae lacus Ut velit enim vestibulum non fermentum nec hendrerit quis leo</p>
  </div>
  <div class="why" style="left:780px">
    <svg width="76" height="66" viewBox="0 0 76 66" fill="none" stroke="#222" stroke-width="2"><rect x="4" y="18" width="42" height="24"/><rect x="8" y="12" width="42" height="24" transform="rotate(-8 29 24)"/><circle cx="25" cy="30" r="6"/><ellipse cx="58" cy="40" rx="12" ry="4"/><path d="M46 40v20c0 2 5 4 12 4s12-2 12-4V40M46 47c0 2 5 4 12 4s12-2 12-4M46 54c0 2 5 4 12 4s12-2 12-4"/></svg>
    <h3>0% Financing for<br>60 months</h3>
    <p>Praesent vitae lacus Ut velit enim vestibulum non fermentum nec hendrerit quis leo</p>
  </div>
</section>

<section class="contact">
  <div class="ph" role="img" aria-label="Dark mountain range backdrop" style="left:0;top:2386px;width:1200px;height:640px;background:linear-gradient(180deg,#2c2c2c,#3a3a3a 55%,#262626)"></div>
  <svg class="abs" style="left:0;top:2378px" width="1200" height="40" viewBox="0 0 1200 40"><polygon points="0,0 1200,0 1200,36 0,8" fill="#fff"/></svg>
  <svg class="abs" style="left:0;top:2930px" width="1200" height="110" viewBox="0 0 1200 110">
    <polygon points="0,10 700,30 0,100" fill="#fdd20a"/>
    <polygon points="0,100 700,30 1200,80 1200,110 0,110" fill="#fff"/>
  </svg>
  <div class="section-title" style="top:2490px;color:#fff">CONTACT US TODAY</div>
  <p class="abs" style="left:280px;top:2538px;width:640px;text-align:center;font-size:16px;line-height:23px;color:#e5e5e5">Fusce tellus Sed metus augue convallis et vehicula ut pulvinar eu ante Integer orci tellus tristique vitae consequat nec porta vel lectus</p>
  <div class="field" style="left:168px;top:2618px;width:280px;height:45px;padding-top:14px">Your Name</div>
  <div class="field" style="left:460px;top:2618px;width:281px;height:45px;padding-top:14px">Email address</div>
  <div class="field" style="left:753px;top:2618px;width:280px;height:45px;padding-top:14px">Phone Number</div>
  <div class="field" style="left:168px;top:2678px;width:865px;height:116px">Message</div>
  <div class="btn" style="left:504px;top:2819px;width:199px;height:53px">SUBMIT NOW</div>
</section>

<section class="blogs">
  <div class="section-title" style="top:3050px">LATEST BLOGS</div>
  <article class="post" style="left:136px">
    <div class="ph img" role="img" aria-label="Wall-mounted mini split above a doorway"></div>
    <div class="ph" style="left:0;top:0;width:299px;height:204px;background:linear-gradient(135deg,#efe6d8,#d8c3a0)"></div>
    <h4>Fusce tellus Sed metus augue</h4>
    <p>convallis et vehicula ut pulvinar eu ante Integer orci tellus tristique vitae</p>
    <div class="more">READ MORE</div>
  </article>
  <article class="post" style="left:460px">
    <div class="ph" role="img" aria-label="Person using a remote in a bright room with plants and a mini split" style="left:0;top:0;width:299px;height:204px;background:linear-gradient(135deg,#f2f2f0,#c9cfc5)"></div>
    <h4>Morbi eget arcu Morbi porta</h4>
    <p>convallis et vehicula ut pulvinar eu ante Integer orci tellus tristique vitae</p>
    <div class="more">READ MORE</div>
  </article>
  <article class="post" style="left:785px">
    <div class="ph" role="img" aria-label="Technician checking pressure gauges on rooftop units" style="left:0;top:0;width:299px;height:204px;background:linear-gradient(135deg,#9aa3ab,#5a6570)"></div>
    <h4>Donec iaculis diam a nisi</h4>
    <p>convallis et vehicula ut pulvinar eu ante Integer orci tellus tristique vitae</p>
    <div class="more">READ MORE</div>
  </article>
</section>

<footer class="site-footer">
  <div class="abs" style="left:150px;top:75px;width:230px;text-align:center">
    <div style="font-size:22px;font-weight:900;color:var(--ink)">Copper Fern Services</div>
    <div style="font-size:21px;font-weight:900;color:var(--ink);margin-top:14px;letter-spacing:.5px">DUCTLESS EXPERTS</div>
  </div>
  <div class="foot-col abs" style="left:442px;top:82px">
    <h5>QUICK LINKS</h5>
    <a>About Us</a><a>Our Services</a><a>Why Us</a><a>Blogs</a><a>Video</a>
  </div>
  <div class="foot-col abs" style="left:615px;top:82px">
    <h5>RESOURCES</h5>
    <a>Financing</a><a>Contact Us</a><a>Privacy Policy</a><a>Site Map</a>
  </div>
  <div class="foot-col abs" style="left:804px;top:82px">
    <h5>CONTACT US</h5>
    <div style="display:flex;gap:10px"><svg width="14" height="20" viewBox="0 0 14 20"><path d="M7 0a7 7 0 0 0-7 7c0 5 7 13 7 13s7-8 7-13a7 7 0 0 0-7-7zm0 10a3 3 0 1 1 0-6 3 3 0 0 1 0 6z" fill="#222"/></svg><span>48 Alder Row #B<br>Salem 97301 OR</span></div>
    <div style="display:flex;gap:10px;margin-top:8px;align-items:center"><svg width="15" height="15" viewBox="0 0 24 24"><path fill="#222" d="M6.6 10.8a15.1 15.1 0 0 0 6.6 6.6l2.2-2.2c.3-.3.7-.4 1-.2 1.1.4 2.3.6 3.6.6.6 0 1 .4 1 1V20c0 .6-.4 1-1 1C10.6 21 3 13.4 3 4c0-.6.4-1 1-1h3.5c.6 0 1 .4 1 1 0 1.3.2 2.5.6 3.6.1.3 0 .7-.2 1z"/></svg><span>(503) 555 0172</span></div>
    <div style="display:flex;gap:10px;align-items:center"><svg width="15" height="12" viewBox="0 0 15 12"><rect width="15" height="12" fill="#222"/><path d="M0 0l7.5 6L15 0" stroke="#fdd20a" fill="none"/></svg><span>hello@copperfern.example</span></div>
  </div>
</footer>
<div class="social" style="left:161px"></div>
<div class="social" style="left:210px"></div>
<div class="social" style="left:258px"></div>
<div class="social" style="left:308px"></div>
<div class="copyright">© 2019 Company Name &nbsp;All right reserved</div>

</body>
</html>
```